Android Payment Application UI Design

We require a UI/UX design for an existing Android card-based payment application.

We're looking to improve the look + feel of the existing app. What we're after:
- Colour palette options
- Fonts
- Icons

See attached document for existing screen types, icons, etc.

All resources provided must be royalty free.

It's to run on a specialised device, with 720 x 1280 pixel resolution, in portrait only (landscape not required).

Please provide mockup examples of the new screen layout applied to the existing screens in the document.

Target Market(s)

Retail business users

Font styles to use
Sans Serif

Colors

Designer to choose colors to be used in the design.

Requirements
Must have
• Looking for
• - modern design
• - simple colours, easy-to-read sans-serif fonts
• - cohesive, consistent design between screens

```html
<!DOCTYPE html>
<html lang="en">
<head>
<meta charset="utf-8">
<title>Veyra Terminal – Main Menu</title>
<link href="https://fonts.googleapis.com/css2?family=Roboto:wght@400;500;700&display=swap" rel="stylesheet">
<style>
  :root {
    --white: #ffffff;
    --ink: #1c1c1c;
    --label: #4a4f57;
    --brand: #8c949c;
    --brand-dot: #2a8fd0;
    --band-top: #123a7a;
    --band-bottom: #2d78bf;
    --tab-muted: rgba(255,255,255,0.22);
    --sky-top: #ffffff;
    --sky-bottom: #6cbde9;
    --card-border: #d6dde4;
    --battery: #c7352c;
  }
  * { box-sizing: border-box; margin: 0; padding: 0; }
  html, body { width: 675px; height: 1200px; overflow: hidden; }
  body { font-family: "Roboto", Arial, sans-serif; background: var(--white); position: relative; }

  .status-bar {
    position: absolute; top: 0; left: 0; width: 675px; height: 58px;
    background: var(--white); color: var(--ink);
    font-size: 22px; display: flex; align-items: center; padding: 0 16px;
  }
  .status-bar .carrier { display: flex; align-items: center; gap: 8px; }
  .status-bar .dots { letter-spacing: -2px; font-size: 18px; }
  .status-bar .time { position: absolute; left: 0; right: 0; text-align: center; font-weight: 500; }
  .status-bar .battery { margin-left: auto; display: flex; align-items: center; gap: 8px; }

  .app-header {
    position: absolute; top: 58px; left: 0; width: 675px; height: 118px;
    background: var(--white);
  }
  .app-header .menu-stack { position: absolute; left: 14px; top: 40px; }
  .app-header .menu-list { position: absolute; right: 18px; top: 42px; }
  .brand {
    position: absolute; left: 0; right: 0; top: 30px;
    display: flex; justify-content: center; align-items: center; gap: 14px;
  }
  .brand .mark { width: 46px; height: 46px; border-radius: 50%; background: var(--brand-dot); }
  .brand .name { font-size: 52px; font-weight: 700; color: var(--brand); letter-spacing: 2px; }

  .tab-band {
    position: absolute; top: 176px; left: 0; width: 675px; height: 128px;
    background: linear-gradient(180deg, var(--band-top), var(--band-bottom));
  }
  .tab { position: absolute; top: 45px; font-size: 27px; }
  .tab.active { left: 100px; color: var(--white); font-weight: 500; }
  .tab.muted { left: 450px; color: var(--tab-muted); }

  .menu-area {
    position: absolute; top: 304px; left: 0; width: 675px; height: 896px;
    background: linear-gradient(180deg, var(--sky-top) 0%, #d7eefa 45%, var(--sky-bottom) 100%);
  }
  .menu-item {
    position: absolute; left: 83px; width: 511px; height: 90px;
    background: var(--white); border: 2px solid var(--card-border); border-radius: 14px;
    display: flex; align-items: center; padding-left: 34px;
    font-size: 17px; color: var(--label);
  }
</style>
</head>
<body>
  <div class="status-bar">
    <div class="carrier"><span class="dots">●●●○○</span><span>Carrier</span>
      <svg width="14" height="20" viewBox="0 0 14 20"><rect x="1" y="1" width="12" height="18" rx="2" fill="none" stroke="#1c1c1c" stroke-width="2"/><rect x="4" y="5" width="6" height="8" fill="#1c1c1c"/></svg>
    </div>
    <div class="time">11:49 AM</div>
    <div class="battery"><span>2%</span>
      <svg width="46" height="22" viewBox="0 0 46 22"><rect x="1" y="1" width="40" height="20" rx="4" fill="none" stroke="#1c1c1c" stroke-width="2"/><rect x="42" y="7" width="3" height="8" rx="1" fill="#1c1c1c"/><rect x="4" y="4" width="3" height="14" fill="var(--battery)"/></svg>
    </div>
  </div>

  <header class="app-header">
    <svg class="menu-stack" width="22" height="32" viewBox="0 0 22 32">
      <ellipse cx="11" cy="5" rx="10" ry="4" fill="#3b3f46"/>
      <path d="M1 8 v6 a10 4 0 0 0 20 0 v-6 a10 4 0 0 1 -20 0z" fill="#3b3f46"/>
      <path d="M1 17 v6 a10 4 0 0 0 20 0 v-6 a10 4 0 0 1 -20 0z" fill="#3b3f46"/>
    </svg>
    <div class="brand"><span class="mark"></span><span class="name">VEYRA</span></div>
    <svg class="menu-list" width="30" height="26" viewBox="0 0 30 26">
      <rect x="0" y="1" width="5" height="5" fill="#3b3f46"/><rect x="9" y="2" width="21" height="3" fill="#3b3f46"/>
      <rect x="0" y="10" width="5" height="5" fill="#3b3f46"/><rect x="9" y="11" width="21" height="3" fill="#3b3f46"/>
      <rect x="0" y="19" width="5" height="5" fill="#3b3f46"/><rect x="9" y="20" width="21" height="3" fill="#3b3f46"/>
    </svg>
  </header>

  <nav class="tab-band">
    <span class="tab active">Main Menu</span>
    <span class="tab muted">Admin Menu</span>
  </nav>

  <main class="menu-area">
    <div class="menu-item" style="top:34px">Sale</div>
    <div class="menu-item" style="top:146px">Reversal</div>
    <div class="menu-item" style="top:261px">Refund</div>
    <div class="menu-item" style="top:373px">Pre-auth</div>
    <div class="menu-item" style="top:486px">Completion</div>
    <div class="menu-item" style="top:598px">Reconciliation</div>
    <div class="menu-item" style="top:711px">Print manager</div>
  </main>
</body>
</html>
```